Brimlow OrthoLink IT Inc. new website

i need a website for my company which is dedicated to installation and service of computer systems in Dental Offices. I would like for it to encompass a technology feel and professional look. The company deals with all aspects of technology like, Audio Visual, computer systems and networks, Cloud services like data backup, data center. We provide manage services, support and services to Dental Professionals.
Updates

Looking for a Technology font but professional look Added Wednesday, April 20, 2016

Target Market(s)

Dental, Dentist

Industry/Entity Type

Dental

Number of Pages Required

5+ page

Font styles to use
Other font styles liked:
• Futuristic or Techy

Colors
0255a3
ec1f27

Requirements
Must have
• Tabs
Nice to have
• Have no idea maybe some suggestion on your part may help
Should not have
• A professional feel but have a techy look

```html
<!DOCTYPE html>
<html lang="en">
<head>
<meta charset="utf-8">
<title>Brimlow OrthoLink IT</title>
<link href="https://fonts.googleapis.com/css2?family=Lato:wght@400;700;900&family=Open+Sans:wght@400;600;700&family=Roboto+Condensed:wght@400;700&display=swap" rel="stylesheet">
<style>
:root{
  --brand:#0255a3;
  --brand-dark:#034a8c;
  --ink:#111;
  --body:#6b6b6b;
  --band:#e9e9e9;
  --footer:#1f1f1f;
  --footer-text:#cfcfcf;
  --white:#fff;
}
*{margin:0;padding:0;box-sizing:border-box}
html,body{width:1200px;height:2624px;overflow:hidden;background:var(--white)}
body{position:relative;font-family:'Open Sans',sans-serif;color:var(--body)}
.abs{position:absolute}
.cond{font-family:'Roboto Condensed',sans-serif}
.lato{font-family:'Lato',sans-serif}

/* header + hero */
.hero{left:0;top:0;width:1200px;height:621px;
  background:linear-gradient(90deg,#fff 0%,#f4f6f9 22%,#d9dee6 48%,#c4ccd8 75%,#dfe3ea 100%)}
.hero-photo{left:360px;top:118px;width:840px;height:503px;
  background:linear-gradient(180deg,rgba(255,255,255,0) 0%,rgba(160,170,185,.25) 60%,rgba(70,75,85,.35) 100%)}
.hero-fade{left:0;top:560px;width:1200px;height:70px;background:linear-gradient(180deg,rgba(255,255,255,0),#fff)}
.logo{left:79px;top:22px;display:flex;align-items:center;gap:12px}
.logo-mark{width:22px;height:22px;background:var(--brand);border-radius:3px}
.logo-name{font-family:'Roboto Condensed',sans-serif;font-weight:700;font-size:30px;color:var(--brand);line-height:1.05;width:230px}
.nav{left:450px;top:33px;display:flex;align-items:center;gap:0}
.nav a{font-family:'Roboto Condensed',sans-serif;font-size:18px;color:#555;text-decoration:none;padding:0 16px;height:46px;line-height:46px;letter-spacing:.3px}
.nav a.active{background:var(--brand);color:#fff;border-radius:3px;padding:0 22px;margin-right:4px}
.header-rule{left:79px;top:117px;width:1044px;height:1px;background:#c9ced6}
.hero-title{left:79px;top:242px;font-family:'Lato',sans-serif;font-weight:900;font-size:45px;line-height:62px;color:#0d0d0d}
.hero-lead{left:79px;top:370px;width:420px;font-family:'Roboto Condensed',sans-serif;font-size:21px;line-height:31px;color:#1a1a1a}
.btn{left:77px;top:455px;width:203px;height:62px;background:var(--brand);color:#fff;border-radius:4px;
  font-family:'Roboto Condensed',sans-serif;font-weight:700;font-size:24px;display:flex;align-items:center;justify-content:center}

/* welcome */
.section-title{left:0;width:1200px;text-align:center;font-size:39px;color:var(--ink)}
.section-title span{color:var(--brand)}
.welcome-title{top:676px;font-family:'Lato',sans-serif}
.welcome-text{left:165px;top:748px;width:870px;text-align:center;font-size:16px;line-height:25px}
.feature{width:330px;text-align:center}
.feature-icon{width:126px;height:126px;border-radius:50%;background:var(--brand);margin:0 auto;display:flex;align-items:center;justify-content:center}
.feature h3{font-family:'Lato',sans-serif;font-weight:400;font-size:22px;line-height:33px;color:var(--ink);margin-top:20px}
.feature p{font-size:15.5px;line-height:25px;margin-top:4px}

/* services band */
.services-band{left:0;top:1203px;width:1200px;height:240px;background:var(--band)}
.service-photo{width:208px;height:136px}
.service-title{font-family:'Roboto Condensed',sans-serif;font-size:28px;color:var(--brand)}
.service-text{width:260px;font-size:15.5px;line-height:25px}

/* support banner */
.support-banner{left:0;top:1443px;width:1200px;height:416px;background:linear-gradient(90deg,#f6f6f6 0%,#eceff2 45%,#dfe3e8 100%)}
.support-photo{left:600px;top:1443px;width:600px;height:416px;background:linear-gradient(90deg,rgba(236,239,242,0) 0%,#c9ced6 40%,#b9c0c9 70%,#d6dadf 100%)}
.support-kicker{left:80px;top:1519px;font-family:'Roboto Condensed',sans-serif;font-size:24px;color:var(--brand)}
.support-title{left:79px;top:1568px;font-family:'Roboto Condensed',sans-serif;font-size:41px;color:var(--brand)}
.call{left:81px;top:1645px;display:flex;align-items:center;gap:20px;font-family:'Roboto Condensed',sans-serif;font-size:30px;color:#222}
.call .num{color:var(--brand);font-weight:700}
.call-icon{width:62px;height:62px;border:2px solid #222;border-radius:50%;display:flex;align-items:center;justify-content:center}

/* testimonials */
.testimonial-title{top:1906px;font-family:'Roboto Condensed',sans-serif;font-size:41px}
.quote-mark{left:576px;top:1983px}
.arrow{width:62px;height:62px;border:2px solid #222;border-radius:50%;display:flex;align-items:center;justify-content:center;top:2028px}
.testimonial-text{left:220px;top:2036px;width:760px;text-align:center;font-size:16px;line-height:26px;color:#333}
.client-name{left:0;top:2140px;width:1200px;text-align:center;font-size:16px;font-weight:700;color:var(--brand)}

/* news */
.news-band{left:0;top:2214px;width:1200px;height:235px;background:var(--band)}
.news-title{top:2246px;font-family:'Roboto Condensed',sans-serif;font-size:43px;letter-spacing:.5px}
.news-item{top:2326px;display:flex;gap:8px;width:330px}
.news-date{width:73px;height:84px;background:var(--brand);color:#fff;text-align:center;flex:none;padding-top:8px}
.news-date b{display:block;font-family:'Roboto Condensed',sans-serif;font-size:32px;line-height:36px}
.news-date small{font-size:15px}
.news-text{font-size:15px;line-height:25px;color:#666}
.news-text b{display:block;font-family:'Open Sans',sans-serif;font-weight:700;font-size:14px;color:#222}

/* footer */
.footer{left:0;top:2449px;width:1200px;height:175px;background:var(--footer)}
.footer-nav{left:79px;top:2476px;display:flex;gap:46px;font-size:16px;color:#9a9a9a}
.footer-nav .active{color:#fff}
.social{top:2481px;left:980px;display:flex;gap:36px}
.social span{width:14px;height:14px;border-radius:50%;background:#fff;display:block}
.footer-rule{left:79px;top:2526px;width:1044px;height:1px;background:#3c3c3c}
.footer-info{top:2550px;display:flex;gap:8px;font-size:15px;line-height:24px;color:var(--footer-text)}
.footer-info .phone{font-weight:700;font-size:21px;color:#fff}
</style>
</head>
<body>

<header>
  <div class="abs hero"></div>
  <div class="abs hero-photo" role="img" aria-label="Bright modern dental treatment room with equipment and an x-ray display"></div>
  <div class="abs hero-fade"></div>
  <div class="abs logo"><span class="logo-mark"></span><span class="logo-name">Brimlow OrthoLink IT</span></div>
  <nav class="abs nav">
    <a class="active">HOME</a><a>ABOUT</a><a>SERVICES</a><a>SUPPORT</a><a>CLIENT</a><a>BLOG</a><a>CONTACT</a>
  </nav>
  <div class="abs header-rule"></div>
  <h1 class="abs hero-title">TECHNOLOGY FOR<br>BEST PRACTICE</h1>
  <p class="abs hero-lead">f you view technology as an expense rather than an investment, you haven’t worked with us.</p>
  <a class="abs btn">CONTACT US</a>
</header>

<section>
  <h2 class="abs section-title welcome-title">Welcome to <span>Brimlow OrthoLink IT</span></h2>
  <p class="abs welcome-text">Lorem Ipsum is simply dummy text of the printing and typesetting industry. Lorem Ipsum has been the industry's standard dummy text ever since the 1500s, when an unknown printer took a galley of type and scrambled it to make a type specimen book.</p>

  <div class="abs feature" style="left:71px;top:862px">
    <div class="feature-icon">
      <svg width="56" height="52" viewBox="0 0 56 52" fill="none" stroke="#fff" stroke-width="3"><rect x="3" y="3" width="50" height="34" rx="2"/><path d="M22 37v8M34 37v8M16 47h24"/><rect x="17" y="11" width="22" height="16" fill="#fff" stroke="none"/><path d="M25 15l7 4-7 4z" fill="#0255a3" stroke="none"/></svg>
    </div>
    <h3>Audio Visual</h3>
    <p>Lorem Ipsum is simply dummy text of the printing and typesetting industry. Lorem Ipsum has been the industry.</p>
  </div>
  <div class="abs feature" style="left:435px;top:862px">
    <div class="feature-icon">
      <svg width="64" height="56" viewBox="0 0 64 56" fill="none" stroke="#fff" stroke-width="3"><rect x="3" y="18" width="24" height="18" rx="2"/><rect x="44" y="3" width="16" height="11" rx="1"/><rect x="44" y="22" width="16" height="11" rx="1"/><rect x="44" y="41" width="16" height="11" rx="1"/><path d="M27 27h8M35 8v39M35 8h9M35 27h9M35 47h9"/></svg>
    </div>
    <h3>Computer Systems and Networks</h3>
    <p>Lorem Ipsum is simply dummy text of the printing and typesetting industry. Lorem Ipsum has been the industry.</p>
  </div>
  <div class="abs feature" style="left:800px;top:862px">
    <div class="feature-icon">
      <svg width="70" height="60" viewBox="0 0 70 60" fill="none" stroke="#fff" stroke-width="3"><path d="M18 38H14a11 11 0 0 1 0-22 16 16 0 0 1 30-4 12 12 0 0 1 16 12"/><ellipse cx="42" cy="30" rx="12" ry="5" fill="#fff"/><path d="M30 30v18c0 3 5 5 12 5s12-2 12-5V30M30 39c0 3 5 5 12 5s12-2 12-5" /><circle cx="56" cy="48" r="7" fill="#0255a3"/><path d="M53 48l2 2 4-4"/></svg>
    </div>
    <h3>Cloud Services of Data Backup</h3>
    <p>Lorem Ipsum is simply dummy text of the printing and typesetting industry. Lorem Ipsum has been the industry.</p>
  </div>
</section>

<section>
  <div class="abs services-band"></div>
  <div class="abs service-photo" style="left:77px;top:1254px;background:linear-gradient(135deg,#e8ecf0,#8a96a6 55%,#3e4654)" role="img" aria-label="Business team reviewing documents at a desk"></div>
  <h3 class="abs service-title" style="left:303px;top:1246px">Manage services</h3>
  <p class="abs service-text" style="left:303px;top:1290px">Lorem Ipsum is simply dummy text of the printing and typesetting industry. Lorem Ipsum has been the industry.</p>
  <div class="abs service-photo" style="left:637px;top:1254px;background:linear-gradient(135deg,#f1f3f5,#c2cad4 50%,#8f99a6)" role="img" aria-label="Support agents wearing headsets"></div>
  <h3 class="abs service-title" style="left:862px;top:1246px">Support</h3>
  <p class="abs service-text" style="left:862px;top:1290px">Lorem Ipsum is simply dummy text of the printing and typesetting industry. Lorem Ipsum has been the industry.</p>
</section>

<section>
  <div class="abs support-banner"></div>
  <div class="abs support-photo" role="img" aria-label="Smiling customer support agent with headset in front of colleagues"></div>
  <p class="abs support-kicker">WHAT ARE YOU WAITING FOR?</p>
  <h2 class="abs support-title">BRIMLOW ORTHOLINK IT SUPPORT</h2>
  <div class="abs call">
    <span>CALL US ON</span>
    <span class="call-icon"><svg width="28" height="28" viewBox="0 0 24 24" fill="#222"><path d="M6.6 10.8a15 15 0 0 0 6.6 6.6l2.2-2.2a1 1 0 0 1 1-.25 11.4 11.4 0 0 0 3.6.57 1 1 0 0 1 1 1V20a1 1 0 0 1-1 1A17 17 0 0 1 3 4a1 1 0 0 1 1-1h3.5a1 1 0 0 1 1 1c0 1.25.2 2.45.57 3.57a1 1 0 0 1-.25 1z"/></svg></span>
    <span class="num">123 456 7890</span>
  </div>
</section>

<section>
  <h2 class="abs section-title testimonial-title">What Our <span>Client Say</span></h2>
  <svg class="abs quote-mark" width="46" height="38" viewBox="0 0 46 38" fill="#555"><path d="M0 38V22C0 10 6 3 17 0l2 5c-6 2-9 6-9 12h9v21zM27 38V22c0-12 6-19 17-22l2 5c-6 2-9 6-9 12h9v21z"/></svg>
  <div class="abs arrow" style="left:77px"><svg width="16" height="28" viewBox="0 0 16 28" fill="none" stroke="#222" stroke-width="2.5"><path d="M14 2L2 14l12 12"/></svg></div>
  <div class="abs arrow" style="left:1057px"><svg width="16" height="28" viewBox="0 0 16 28" fill="none" stroke="#222" stroke-width="2.5"><path d="M2 2l12 12L2 26"/></svg></div>
  <p class="abs testimonial-text">Lorem Ipsum is simply dummy text of the printing and typesetting industry. Lorem Ipsum has been the industry's standard dummy text ever since the 1500.Lorem Ipsum is simply dummy text of the printing and typesetting industry.</p>
  <p class="abs client-name">- Client Name</p>
</section>

<section>
  <div class="abs news-band"></div>
  <h2 class="abs section-title news-title">LATEST <span>NEWS</span></h2>
  <article class="abs news-item" style="left:79px">
    <div class="news-date"><b>21</b><small>Apr</small></div>
    <p class="news-text">Lorem Ipsum is simply dummy text of the print &amp; typesetting industry.<b>READ MORE</b></p>
  </article>
  <article class="abs news-item" style="left:434px">
    <div class="news-date"><b>20</b><small>Apr</small></div>
    <p class="news-text">Lorem Ipsum is simply dummy text of the print &amp; typesetting industry.<b>READ MORE</b></p>
  </article>
  <article class="abs news-item" style="left:799px">
    <div class="news-date"><b>19</b><small>Apr</small></div>
    <p class="news-text">Lorem Ipsum is simply dummy text of the print &amp; typesetting industry.<b>READ MORE</b></p>
  </article>
</section>

<footer>
  <div class="abs footer"></div>
  <nav class="abs footer-nav"><span class="active">Home</span><span>About</span><span>Services</span><span>Support</span><span>News</span><span>Contact</span></nav>
  <div class="abs social" aria-label="Social links"><span></span><span></span><span></span></div>
  <div class="abs footer-rule"></div>
  <div class="abs footer-info" style="left:79px">
    <svg width="14" height="20" viewBox="0 0 14 20" fill="#fff" style="margin-top:3px"><path d="M7 0a7 7 0 0 0-7 7c0 5 7 13 7 13s7-8 7-13a7 7 0 0 0-7-7zm0 10a3 3 0 1 1 0-6 3 3 0 0 1 0 6z"/></svg>
    <span style="width:210px">Lorem Ipsum is simply dummy text of the printing.</span>
  </div>
  <div class="abs footer-info" style="left:350px;top:2551px;align-items:center">
    <svg width="20" height="20" viewBox="0 0 24 24" fill="#fff"><path d="M6.6 10.8a15 15 0 0 0 6.6 6.6l2.2-2.2a1 1 0 0 1 1-.25 11.4 11.4 0 0 0 3.6.57 1 1 0 0 1 1 1V20a1 1 0 0 1-1 1A17 17 0 0 1 3 4a1 1 0 0 1 1-1h3.5a1 1 0 0 1 1 1c0 1.25.2 2.45.57 3.57a1 1 0 0 1-.25 1z"/></svg>
    <span class="phone">123 456 7890</span>
  </div>
  <div class="abs footer-info" style="left:621px;align-items:center">
    <svg width="20" height="15" viewBox="0 0 20 15" fill="none" stroke="#fff" stroke-width="1.6"><rect x="1" y="1" width="18" height="13" rx="1"/><path d="M1 2l9 7 9-7"/></svg>
    <span>info@brimlowortholink.com</span>
  </div>
  <div class="abs footer-info" style="left:891px;width:240px">
    <span>© <b style="color:#fff">BRIMLOW ORTHOLINK IT</b> - 2016.<br>All Rights Reserved.</span>
  </div>
</footer>

</body>
</html>
```